Brantor Works Business Card

Modern and Professional Business Card for a Med size construction/development company.

See the samples below for the design I like … but I need ideas for incorporating the red company logo while still keeping the clean look of the card samples that are attached.

Logo and tag line on the back … info on the front.

Tagline: Quality Starts from the Ground Up

Target Market(s)

Med-Large General Contractors

Contact Information for Business Card

Brantor Works Limited
42 Fenwick Avenue
Mt. Pearl, NL
A1N 4R9

t: 709-555-0147
f: 709-555-0182
w: www.brantorworks-example.com

Font styles to use
Sans Serif

Colors
fbee3e

Requirements
Must have
• I like the black and yellow designs of the attached samples …. but I'm not sure how to incorporate the red Brantor Works logo into that design??
Nice to have
• Construction safety strips

```html
<!DOCTYPE html>
<html lang="en">
<head>
<meta charset="utf-8">
<title>Brantor Works Limited – Business Card</title>
<link href="https://fonts.googleapis.com/css2?family=Arimo:wght@400;700&display=swap" rel="stylesheet">
<style>
  :root {
    --backdrop: #e9e9e9;
    --card-red: #e00d12;
    --safety-yellow: #fbc61a;
    --safety-black: #111111;
    --tear-white: #f7f7f4;
    --text-yellow: #fbee3e;
    --ink: #111111;
  }
  * { margin: 0; padding: 0; box-sizing: border-box; }
  html, body {
    width: 1200px; height: 720px; overflow: hidden;
    background: var(--backdrop);
    font-family: "Arimo", Arial, sans-serif;
  }
  .card-set {
    position: absolute; inset: 0;
    display: flex; align-items: center; justify-content: center; gap: 60px;
  }
  .card {
    position: relative; width: 500px; height: 290px;
    box-shadow: 0 6px 18px rgba(0,0,0,.18);
    overflow: hidden;
  }
  .card-art { position: absolute; inset: 0; width: 100%; height: 100%; display: block; }

  .front-content { position: absolute; left: 34px; top: 150px; }
  .company-name {
    color: var(--text-yellow); font-weight: 700; font-size: 27px;
    letter-spacing: .3px; line-height: 1; white-space: nowrap;
  }
  .contact-list {
    list-style: none; display: flex; gap: 14px; margin-top: 12px;
    color: var(--tear-white); font-size: 11.5px; white-space: nowrap;
  }
  .contact-list li { display: flex; align-items: center; gap: 5px; }
  .contact-icon {
    width: 13px; height: 13px; background: var(--text-yellow);
    display: inline-flex; align-items: center; justify-content: center;
  }
  .contact-icon svg { width: 9px; height: 9px; }

  .back-content {
    position: absolute; left: 0; right: 0; top: 128px;
    display: flex; justify-content: center;
  }
  .brand-name {
    color: var(--ink); font-weight: 700; font-size: 28px; letter-spacing: .5px;
    text-transform: uppercase; line-height: 1; white-space: nowrap;
  }
</style>
</head>
<body>
<svg width="0" height="0" style="position:absolute" aria-hidden="true">
  <defs>
    <pattern id="hazard" width="36" height="36" patternUnits="userSpaceOnUse" patternTransform="rotate(40)">
      <rect width="36" height="36" fill="var(--safety-yellow)"/>
      <rect width="16" height="36" fill="var(--safety-black)"/>
    </pattern>
  </defs>
</svg>

<main class="card-set">
  <section class="card card-front">
    <svg class="card-art" viewBox="0 0 500 290" aria-hidden="true">
      <rect width="500" height="290" fill="var(--card-red)"/>
      <polygon class="tear-edge" fill="var(--tear-white)"
        points="0,0 500,0 500,10 470,14 440,12 400,18 360,20 320,22 280,27 240,26 200,31 160,34 120,36 80,40 40,42 0,47"/>
      <polygon class="safety-strip" fill="url(#hazard)"
        points="0,0 500,0 500,5 466,8 434,7 396,12 356,14 316,17 276,21 236,20 196,25 156,28 116,30 76,34 36,36 0,40"/>
      <polygon class="tear-edge" fill="var(--tear-white)"
        points="0,290 0,268 40,266 80,258 120,256 160,247 200,244 240,236 280,230 320,222 360,218 400,210 440,206 470,198 500,190 500,290"/>
      <polygon class="safety-strip" fill="url(#hazard)"
        points="0,290 0,276 40,273 80,266 120,263 160,255 200,252 240,244 280,238 320,230 360,226 400,218 440,214 470,206 500,198 500,290"/>
    </svg>
    <div class="front-content">
      <h1 class="company-name">BRANTOR WORKS LIMITED</h1>
      <ul class="contact-list">
        <li><span class="contact-icon"><svg viewBox="0 0 10 10"><path d="M2 1h2l1 2-1 1c.6 1.2 1.4 2 2.6 2.6l1-1 2 1v2c0 .5-.5 1-1 1C4.5 9.6.4 5.5 1 2c0-.5.5-1 1-1z" fill="var(--card-red)"/></svg></span>709-555-0147</li>
        <li><span class="contact-icon"><svg viewBox="0 0 10 10"><rect x="1" y="4" width="8" height="4" fill="var(--card-red)"/><rect x="3" y="1" width="4" height="3" fill="var(--card-red)"/></svg></span>709-555-0182</li>
        <li><span class="contact-icon"><svg viewBox="0 0 10 10"><circle cx="5" cy="5" r="4" fill="none" stroke="var(--card-red)" stroke-width="1.2"/><path d="M1 5h8M5 1c-2 2-2 6 0 8M5 1c2 2 2 6 0 8" fill="none" stroke="var(--card-red)" stroke-width=".9"/></svg></span>www.brantorworks-example.com</li>
      </ul>
    </div>
  </section>

  <section class="card card-back">
    <svg class="card-art" viewBox="0 0 500 290" aria-hidden="true">
      <rect width="500" height="290" fill="var(--card-red)"/>
      <polygon class="tear-edge" fill="var(--tear-white)"
        points="0,0 500,0 500,8 470,14 440,22 400,30 360,40 320,48 280,56 240,66 200,74 160,82 120,92 80,100 40,108 0,118"/>
      <polygon class="safety-strip" fill="url(#hazard)"
        points="0,0 500,0 500,2 466,8 434,15 396,23 356,33 316,41 276,49 236,58 196,66 156,74 116,84 76,92 36,100 0,110"/>
      <polygon class="tear-edge" fill="var(--tear-white)"
        points="160,290 190,284 230,272 270,262 310,248 350,236 390,220 430,208 470,192 500,182 500,290"/>
      <polygon class="safety-strip" fill="url(#hazard)"
        points="172,290 200,286 238,276 278,266 318,254 356,242 396,228 436,216 474,200 500,192 500,290"/>
    </svg>
    <div class="back-content">
      <p class="brand-name">Brantor Works</p>
    </div>
  </section>
</main>
</body>
</html>
```